Logo, Web and Mobile Designs for enterprise social media platform

All the details are in the attached document, please start reading the scope document first which explains what is this project about and the details about the needed deliverables, after that please read the UI_Requirements document which will detail what is expected regarding the coded web version since this is a coded contest, it is very important that you meet the UI requirements or suggest something else but we will need to agree first before working on the coded version

Good Luck

Target Market(s)

Enterprise Social Media

Industry/Entity Type

Media

Coding

Coded - Design and coding required

Number of Pages Required

5+ page

Font styles to use
Sans Serif

Requirements
Must have
• All the must haves are listed in the scope document so please check before you start

```html
<!DOCTYPE html>
<html lang="en">
<head>
<meta charset="utf-8">
<title>Teamora — Enterprise Social Platform</title>
<link rel="stylesheet" href="https://fonts.googleapis.com/css2?family=Open+Sans:wght@400;600;700&family=Cinzel:wght@400;600&display=swap">
<style>
:root{
  --teal:#2aa3c4;
  --teal-dark:#1d7f99;
  --gold:#9c7422;
  --gold-light:#b88e35;
  --ink:#2b2b2b;
  --text:#6a6a6a;
  --muted:#9a9a9a;
  --line:#e3e3e3;
  --red:#d8352a;
  --topbar:#3a3a3a;
  --navy:#16304a;
  --footer:#232323;
  --footer-bottom:#1a1a1a;
  --bg:#fafafa;
}
*{box-sizing:border-box;margin:0;padding:0}
html,body{width:1200px;height:2287px;overflow:hidden}
body{font-family:"Open Sans",Arial,sans-serif;color:var(--text);background:var(--bg);position:relative;font-size:13px}
a{color:inherit;text-decoration:none}
.abs{position:absolute}

/* top bar */
.topbar{left:0;top:0;width:1200px;height:40px;background:linear-gradient(#474747,#2e2e2e)}
.topbar .mark{left:98px;top:10px;width:28px;height:20px;background:var(--teal);border-radius:2px}
.topbar .search{left:235px;top:9px;width:235px;height:22px;background:#fff;border-radius:3px;font-size:10px;font-style:italic;color:#888;padding:4px 18px}
.topbar .search-btn{left:476px;top:9px;width:43px;height:22px;background:var(--teal);border-radius:3px}
.topbar .user{left:869px;top:12px;color:#eee;font-size:11px}
.topbar .ic{top:12px;width:16px;height:14px;background:#9a9a9a;border-radius:3px}
.topbar .badge{top:7px;width:8px;height:8px;border-radius:50%;background:var(--red)}

/* header */
.header{left:0;top:40px;width:1200px;height:132px;background:#fff}
.logo{left:100px;top:58px;display:flex;align-items:center;gap:14px}
.logo .dot{width:50px;height:50px;border-radius:50%;background:var(--teal)}
.logo .name{font-family:"Cinzel",serif;font-size:31px;font-weight:600;color:#333;letter-spacing:1px}
.nav{top:76px;left:606px;display:flex;gap:36px;font-size:12px;color:#444;text-transform:uppercase}
.nav span::before{content:"";display:inline-block;width:9px;height:9px;background:#666;border-radius:2px;margin-right:7px;vertical-align:-1px}
.btn{display:flex;align-items:center;justify-content:center;color:#fff;font-weight:700;font-size:12px;text-transform:uppercase;border-radius:3px}
.login{left:869px;top:117px;width:142px;height:35px;background:linear-gradient(var(--teal),var(--teal-dark))}
.register{left:998px;top:117px;width:101px;height:35px;background:linear-gradient(var(--gold-light),var(--gold))}

/* hero */
.hero{left:0;top:172px;width:1200px;height:473px;background:linear-gradient(90deg,#e9ecef 0%,#6d7f92 30%,#1f3d5c 55%,var(--navy) 100%)}
.hero-photo{left:0;top:172px;width:700px;height:473px;background:linear-gradient(160deg,#dfe3e7 0%,#8a7060 35%,#3c4a5c 70%,rgba(22,48,74,0) 100%)}
.hero h1{left:713px;top:305px;font-family:"Cinzel",serif;font-weight:400;color:#fff;font-size:28px;letter-spacing:.5px}
.hero-text{left:713px;top:352px;width:390px;color:#dbe4ee;font-size:12.5px;line-height:26px}
.viewmore{left:956px;top:472px;width:145px;height:40px;background:linear-gradient(var(--gold-light),var(--gold))}
.arrow{top:385px}

/* sections */
.h2{font-size:22px;font-weight:700;color:var(--ink);text-transform:uppercase}
.h2::after{content:"";display:block;width:50px;height:3px;background:var(--teal);margin-top:10px}
.feature-title{left:99px;top:757px;width:590px;font-size:17px;font-weight:600;color:var(--ink);line-height:26px}
.meta{left:99px;top:817px;font-size:12.5px}
.img{background:linear-gradient(135deg,#e9edf1,#8d98a4 60%,#4a5564)}
.excerpt{left:99px;top:1148px;width:585px;font-size:12px;line-height:24px}
.actions{left:99px;top:1218px;width:581px;height:43px;border:1px solid var(--line);background:#fff;display:flex;align-items:center;padding:0 10px;gap:24px;font-size:12px}
.actions .more{color:var(--teal-dark);text-decoration:underline;font-weight:600}
.actions .share{display:flex;gap:3px;margin-left:auto}
.actions .share i{width:35px;height:20px;background:#8a8f96;display:block}
.actions .share i:last-child{background:#fff;border:1px solid #ccc;width:52px}
.dotted{height:0;border-top:1px dashed #cfcfcf}
.card-title{font-size:13.5px;font-weight:700;color:var(--ink);line-height:20px;width:278px}
.card-text{font-size:12px;line-height:20px;width:275px;margin-top:10px}
.card-meta{border-top:1px solid var(--line);margin-top:10px;padding-top:8px;font-size:10px;display:flex;gap:28px;width:275px}

/* sidebar */
.box{background:#fff;border:1px solid var(--line)}
.follow-head{font-size:12.5px;color:#666}
.follow-head b{color:var(--red);font-weight:400}
.person{display:flex;gap:14px;margin-top:20px}
.person .av{width:90px;height:72px;background:linear-gradient(135deg,#dde2e7,#8a96a3);border:1px solid #ddd}
.person .n{font-size:12px;font-weight:700;color:#444}
.person .n span{font-weight:400;color:var(--muted)}
.person .f{font-size:11px;color:#aaa;margin-top:4px}
.person .f b{color:var(--red);font-weight:400}
.follow-btn{margin-top:6px;width:88px;height:24px;border:1px solid #ccc;background:linear-gradient(#fff,#eee);font-size:12px;color:#444;display:flex;align-items:center;gap:7px;padding-left:10px}
.follow-btn i{width:12px;height:12px;background:#777;display:block}
.grid{display:grid;grid-template-columns:repeat(3,98px);gap:4px;margin-top:22px}
.grid div{height:76px;background:linear-gradient(135deg,#e6eaee,#98a3ae)}
.newsletter{left:769px;top:1430px;width:331px;height:192px;background:linear-gradient(#41bfdd,#2aa3c4);padding:20px 37px;color:#fff}
.newsletter h3{font-size:14px;font-weight:700}
.newsletter p{font-size:12px;line-height:20px;margin-top:10px}
.newsletter .field{margin-top:14px;width:250px;height:30px;background:#fff;color:#777;font-size:10px;font-style:italic;padding:8px 12px}
.newsletter .submit{margin-top:12px;width:96px;height:28px;background:linear-gradient(#1f7d96,#155f73);font-size:12px}

/* latest posts */
.post-title{font-size:13px;font-weight:700;color:var(--ink);text-transform:uppercase}
.post-text{font-size:12px;line-height:22px;width:290px;margin-top:10px}
.post-more{display:inline-block;margin-top:6px;color:var(--teal-dark);text-decoration:underline;font-weight:600;font-size:12.5px}

/* footer */
.footer{left:0;top:1977px;width:1200px;height:258px;background:var(--footer)}
.fcol{top:2013px;width:265px;color:#ccc;font-size:11.5px;line-height:20px}
.fcol h4{font-size:13px;color:#fff;font-weight:700;display:flex;justify-content:space-between;margin-bottom:14px}
.fcol h4 span{color:#888;font-weight:400}
.fcol .c{color:#aaa;margin:4px 0 18px;font-size:11px}
.fcol strong{color:#fff}
.bottom{left:0;top:2235px;width:1200px;height:52px;background:var(--footer-bottom);color:#888;font-size:12px;display:flex;align-items:center;padding:0 95px}
.socials{margin-left:auto;display:flex;gap:12px;align-items:center}
.socials i{width:24px;height:24px;background:#4d5560;border-radius:3px;display:block}
</style>
</head>
<body>

<div class="abs topbar">
  <div class="abs mark"></div>
  <div class="abs search">Search...</div>
  <div class="abs search-btn"></div>
  <div class="abs user">Daniel Reyes &nbsp;▾</div>
  <div class="abs ic" style="left:991px"></div><div class="abs badge" style="left:1002px"></div>
  <div class="abs ic" style="left:1031px"></div>
  <div class="abs ic" style="left:1070px"></div><div class="abs badge" style="left:1081px"></div>
</div>

<header class="abs header"></header>
<div class="abs logo"><div class="dot"></div><span class="name">TEAMORA</span></div>
<nav class="abs nav"><span>Home</span><span>About</span><span>Events</span><span>News</span><span>Contacts</span></nav>
<a class="abs btn login">Login</a>
<a class="abs btn register">Register</a>

<section class="abs hero"></section>
<div class="abs hero-photo" role="img" aria-label="Smiling woman working on a laptop with floating network icons"></div>
<h1 class="abs" style="left:713px;top:305px;font-family:'Cinzel',serif;font-weight:400;color:#fff;font-size:28px">WELCOME TO TEAMORA</h1>
<p class="abs hero-text">Sed ut perspiciatis unde omnis iste natus error sit voluptatemaccuum doloremque laudantium, totam rem aperiam, eaque ipsa quae ab illo inventore veritatis et quasi architecto beatae vitae cta sunt explicabo. Nemim ipsa quia voluptas sit aspernatur a ut odit aut fugit, sed quia</p>
<a class="abs btn viewmore">View More &gt;&gt;</a>
<svg class="abs arrow" style="left:32px" width="16" height="44"><path d="M14 2 L3 22 L14 42" fill="none" stroke="#cfd6dd" stroke-width="1.5"/></svg>
<svg class="abs arrow" style="left:1150px" width="16" height="44"><path d="M2 2 L13 22 L2 42" fill="none" stroke="#cfd6dd" stroke-width="1.5"/></svg>

<!-- latest events -->
<h2 class="abs h2" style="left:98px;top:690px">Latest Events</h2>
<h3 class="abs feature-title">Voluptatem accusantium doloremque laudantium, totam rem aperie eaqu ipsa qub illo inventore doloremque</h3>
<div class="abs meta">By Editor &nbsp;&nbsp;| &nbsp;&nbsp;March 24, 2015</div>
<div class="abs img" style="left:99px;top:852px;width:581px;height:276px" role="img" aria-label="Two businessmen reviewing a tablet at a desk"></div>
<p class="abs excerpt">Voluptatum deleniti atque corrupti quos dolores et quas molestias exceptur occaecaticca ecupid idttent, similique sunt in culpa qui officia deserunt mollitia...</p>
<div class="abs actions">
  <a class="more">Read More &gt;&gt;</a><span>(0) Comments</span><span>02 dec 2015</span><span>Likes</span>
  <div class="share"><i></i><i></i><i></i><i></i></div>
</div>
<div class="abs dotted" style="left:99px;top:1298px;width:581px"></div>

<article class="abs" style="left:99px;top:1337px">
  <div class="img" style="width:275px;height:159px" role="img" aria-label="Businessman with a laptop in an office"></div>
  <h4 class="card-title" style="margin-top:14px">Voluptatemaccusantiumdoloremqlau dantiu totam rem doloremqla</h4>
  <p class="card-text">Nemo enim ipsam voluptatem quia voluptas sit aspernatur aut odit aut ...</p>
  <div class="card-meta"><span>27 March 2015</span><span>120</span><span>203</span><span>18</span></div>
</article>
<article class="abs" style="left:404px;top:1337px">
  <div class="img" style="width:276px;height:159px" role="img" aria-label="Two colleagues working together at a laptop"></div>
  <h4 class="card-title" style="margin-top:14px">Voluptatemaccusantiumdoloremqlau dantiu totam rem doloremqla</h4>
  <p class="card-text">Nemo enim ipsam voluptatem quia voluptas sit aspernatur aut odit aut ...</p>
  <div class="card-meta"><span>27 March 2015</span><span>120</span><span>203</span><span>18</span></div>
</article>

<!-- sidebar -->
<aside class="abs box" style="left:769px;top:718px;width:331px;height:352px;padding:18px 14px">
  <div class="follow-head">Who to Follow &nbsp;- <b>Refresh</b> - <b>View all</b></div>
  <div class="person"><div class="av" role="img" aria-label="Handshake photo"></div><div><div class="n">Marcus Hale <span>@Marcus Hale</span></div><div class="f">Followed by <b>The Harbor</b> and <b>others</b></div><div class="follow-btn"><i></i>Follow</div></div></div>
  <div class="person"><div class="av" role="img" aria-label="Profile photo"></div><div><div class="n">Marcus Hale <span>@Marcus Hale</span></div><div class="f">Followed by <b>The Harbor</b> and <b>others</b></div><div class="follow-btn"><i></i>Follow</div></div></div>
  <div class="person"><div class="av" role="img" aria-label="Profile photo"></div><div><div class="n">Marcus Hale <span>@Marcus Hale</span></div><div class="f">Followed by <b>The Harbor</b> and <b>others</b></div><div class="follow-btn"><i></i>Follow</div></div></div>
</aside>
<aside class="abs box" style="left:769px;top:1100px;width:331px;height:292px;padding:22px 13px">
  <div style="font-size:12.5px;font-weight:700;color:#555">BUSINESS OPPORTUNITIES</div>
  <div class="grid" role="img" aria-label="Six business photos of office meetings and colleagues"><div></div><div></div><div></div><div></div><div></div><div></div></div>
  <svg width="300" height="30" style="margin-top:14px"><circle cx="152" cy="15" r="10" fill="none" stroke="#aaa" stroke-width="3" stroke-dasharray="3 4"/></svg>
</aside>
<div class="abs newsletter">
  <h3>NEWSLETTER</h3>
  <p>Join the 12,000 others and Subscribe to the newsletter.Get all latest News</p>
  <div class="field">Enter Your Email</div>
  <div class="btn submit">Submit</div>
</div>

<div class="abs dotted" style="left:99px;top:1685px;width:1000px"></div>

<!-- latest posts -->
<h2 class="abs h2" style="left:98px;top:1715px">Latest Posts</h2>
<div class="abs img" style="left:99px;top:1783px;width:162px;height:132px" role="img" aria-label="Hands reviewing charts beside a laptop"></div>
<div class="abs" style="left:286px;top:1784px">
  <div class="post-title">Voluptatemaccusantium</div>
  <p class="post-text">Sed ut perspiciatis unde omnis iste nas error sit voluptatem aum doloremaudantium,doloremque laudanti totam rem aperiam...</p>
  <a class="post-more">Read More &gt;&gt;</a>
</div>
<div class="abs img" style="left:636px;top:1783px;width:161px;height:132px" role="img" aria-label="Team meeting around a table"></div>
<div class="abs" style="left:822px;top:1784px">
  <div class="post-title">Voluptatemaccusantium</div>
  <p class="post-text">Sed ut perspiciatis unde omnis iste nas error sit voluptatem aum doloremaudantium,doloremque laudanti totam rem aperiam...</p>
  <a class="post-more">Read More &gt;&gt;</a>
</div>

<!-- footer -->
<footer class="abs footer"></footer>
<div class="abs fcol" style="left:98px">
  <h4>UPDATES <span>‹ ›</span></h4>
  <p>Ipsam voluptatem quia voluptas sit aspernatur aut<br><strong>odit aut fugit, sed quia</strong></p>
  <p class="c">120 Comments</p>
  <p>Ipsam voluptatem quia voluptas sit aspernatur aut<br><strong>odit aut fugit, sed quia</strong></p>
  <p class="c">120 Comments</p>
</div>
<div class="abs fcol" style="left:468px">
  <h4>COMMUNITY <span>‹ ›</span></h4>
  <p>Ipsam voluptatem quia voluptas sit aspernatur aut<br><strong>odit aut fugit, sed quia</strong></p>
  <p class="c">120 Comments</p>
  <p>Ipsam voluptatem quia voluptas sit aspernatur aut<br><strong>odit aut fugit, sed quia</strong></p>
  <p class="c">120 Comments</p>
</div>
<div class="abs fcol" style="left:830px">
  <h4>LATEST NEWS <span>‹ ›</span></h4>
  <p><strong>Ipsam voluptatem quia voluptas sit aspernatur aut odit aut fugit, sed quia</strong></p>
  <p style="margin-top:10px;color:#aaa;font-size:11px">A major Mexican operators was on the mission to Excel in revenue assurance process. The challenge was to confirm that 100% of input CDRs = 100% of output CDRs; its whereabouts?, its status?, how to save traffic approaching 90 days old?</p>
</div>
<div class="abs bottom">©Copyright 2015 -Teamora .com All rights reserved.
  <div class="socials"><i></i><i></i><i></i><i></i><span style="font-size:11px">C22</span></div>
</div>

</body>
</html>
```